Collectibles expert needs a new business card design.

My current business card makes me look to high end. It may even make me look arrogant or too stuffy. I do work with high end clients and their items but most of my business is with average people with average items. My business name is Walter Brennick's Old Orchard Salvage Co. The idea was that I mine the streets helping people discover the treasures buried in their homes. That could be art, jewelry, coins, etc. The name and an older logo I used does not make immediate sense to most people. I tried to go with just my picture and name and that is the current card I am changing. I help people who need to downsize. Whether they are getting rid of one item, a collection or a house full of items I help them discover what they have, what it is worth and what are the best ways we can get the most for them. This may be a combination of estate sale (which I dont do) auction or sell directly to a dealer or collector. Usually it is a combination of these. My main goal is to help make sure they dont accidently sell a Picasso painting in a garage sale. I am uploading a copy of my old card and the old logo I used to use but the winning card design will need to be much different than these. You can learn a little more about me at www.walterjbrennick.example, www.oldorchardsalv.example and www.facebook.com/oosalco. I hope someone can look at what I do and come up with a very unique design that will be equally effective if my client is high income or if my client is low to mid income. I do not care if it is a one or two sided card as long as it conveys my contact information and a good representation of what I do.

Target Market(s)

People who are getting rid of items. These can be elderly couples or individuals that are moving to an active living community and will have less space so they need to sell items. This can also include the children of elder parents that dont want their stuff and want to find solutions to help them get rid of their items.

Contact Information for Business Card

The card should have my business name Walter Brennick's Old Orchard Salvage Co., phone number 555-302-71938, email walter@oldorchardsalvage.example and website www.oldorchardsalvage.example. Would also like to include Buyer, Broker, Consultant and Appraiser. We can put Walter J. Brennick, ISA on the opposite side of the company name since it includes my name as well.

Font styles to use
Sans Serif

Colors

Designer to choose colors to be used in the design.

Requirements
Must have
• My project must have a professional look. It must not alienate low income clients and should still be appealing to high value clients.

```html
<!DOCTYPE html>
<html lang="en">
<head>
<meta charset="utf-8">
<title>Old Orchard Salvage Co. — Business Card</title>
<link rel="stylesheet" href="https://fonts.googleapis.com/css2?family=Lato:wght@400&family=Oswald:wght@600&display=swap">
<style>
  :root {
    --navy: #1f3f63;
    --navy-ring: #274a72;
    --paper: #f7f7f7;
    --grey-mark: #7a7a7a;
    --backdrop: #2b2b2b;
    --white: #ffffff;
    --rule: rgba(255,255,255,0.55);
  }
  * { margin: 0; padding: 0; box-sizing: border-box; }
  html, body { width: 1200px; height: 896px; overflow: hidden; }
  body {
    background: var(--backdrop);
    display: flex;
    flex-direction: column;
    align-items: center;
    justify-content: center;
    gap: 56px;
    font-family: "Lato", Arial, sans-serif;
  }
  .card {
    width: 630px;
    height: 360px;
    position: relative;
    overflow: hidden;
    box-shadow: 0 10px 24px rgba(0,0,0,0.45);
  }
  /* Front */
  .card-front {
    background: var(--paper);
    display: flex;
    flex-direction: column;
    align-items: center;
    justify-content: center;
    gap: 18px;
  }
  .brand-dot {
    width: 96px; height: 96px;
    border: 6px solid var(--grey-mark);
    border-radius: 50%;
  }
  .brand-name {
    font-family: "Oswald", Arial, sans-serif;
    font-weight: 600;
    color: var(--navy);
    font-size: 30px;
    line-height: 1.15;
    text-align: center;
    text-transform: uppercase;
    letter-spacing: 0.5px;
  }
  /* Back */
  .card-back {
    background: var(--navy);
    color: var(--white);
  }
  .back-ring {
    position: absolute;
    left: 250px; top: 70px;
    width: 250px; height: 250px;
    border: 18px solid var(--navy-ring);
    border-radius: 50%;
  }
  .contact-block {
    position: absolute;
    left: 235px; top: 92px;
    width: 330px;
    text-align: center;
  }
  .person-name {
    font-family: "Oswald", Arial, sans-serif;
    font-weight: 600;
    font-size: 27px;
    text-transform: uppercase;
    letter-spacing: 0.3px;
    line-height: 1.1;
  }
  .person-role {
    font-size: 15.5px;
    margin-top: 4px;
  }
  .divider {
    width: 220px;
    height: 1px;
    background: var(--rule);
    margin: 14px auto 12px;
  }
  .contact-line {
    font-size: 15.5px;
    line-height: 1.35;
  }
</style>
</head>
<body>
  <section class="card card-front" aria-label="Card front">
    <div class="brand-dot" aria-hidden="true"></div>
    <h1 class="brand-name">Walter Brennick's<br>Old Orchard Salvage Co.</h1>
  </section>

  <section class="card card-back" aria-label="Card back">
    <div class="back-ring" aria-hidden="true"></div>
    <div class="contact-block">
      <h2 class="person-name">Walter J. Brennick, ISA</h2>
      <p class="person-role">Buyer, Broker, Consultant and Appraiser</p>
      <div class="divider"></div>
      <p class="contact-line">P: 555-302-71938</p>
      <p class="contact-line">E: walter@oldorchardsalvage.example</p>
      <p class="contact-line">www.oldorchardsalvage.example</p>
    </div>
  </section>
</body>
</html>
```